3 Beispiel-Abbildungen für shop Kategorien
Zielgruppe
Entscheider und Ihre AssistentInnen im Marketing / Vertrieb von Firmen aller Branchen und Größen
Aufgabenstellung
Für einen B2B shop benötigen wir Piktogramme / Abbildungen / Grafiken für Kategorien (Produktlinien, Produktgruppen, Dienstleistungen...)
Mit einer eigenständig entwickelten Navi führen wir den Kunden direkt zu den Produkten und zeigen dabei immer die Alternativen. Viel Wert haben wir auf die Aktikelbeschreibungen und Abbildungen gelegt. Wolfram.de will ein Fachgeschäft im Internet sein.
Die Abbildungen sollen aus einem Guß sein und zum CI der Seite passen. Da es am Ende ca. 300 Abbildungen sein werden, (mache sind doppelt, viele unterscheiden sich nur wenig) muss das Konzept einfach sein. Die Gesamt-Kosten sollten sich taxieren lassen und die Realisiierung sollte in insgesamt 8-12 Wochen hochgeladen sein.
Der Designer / die Desingerin sollte davon ausgehen, dass auch die Folgeaufträge zu machen (oder zu vergeben) sind.

```html
<!DOCTYPE html>
<html lang="de">
<head>
<meta charset="utf-8">
<title>Shop-Kategorien – Welt-Edition</title>
<link rel="stylesheet" href="https://fonts.googleapis.com/css2?family=Open+Sans:wght@400;600&family=Arimo:wght@400;700&display=swap">
<style>
  :root {
    --page-blue: #0d79b0;
    --header-dark: #0f2a4a;
    --header-mid: #1d4470;
    --tab-blue: #3a8ee0;
    --tab-blue-dark: #1d5fa6;
    --green: #79b43a;
    --green-light: #93c955;
    --green-pale: #e5f1d8;
    --white: #ffffff;
    --text: #222222;
    --muted: #9fb0c4;
    --rule: #d9d9d9;
    --map-orange: #f3951f;
    --map-yellow: #ffc34d;
  }
  * { box-sizing: border-box; margin: 0; padding: 0; }
  html, body { width: 1200px; height: 481px; overflow: hidden; }
  body {
    background: var(--page-blue);
    position: relative;
    font-family: "Arimo", Arial, sans-serif;
    color: var(--text);
  }
  .column { position: absolute; top: 14px; bottom: 0; background: var(--white); }
  .col-products { left: 19px; width: 299px; }
  .col-maps { left: 324px; width: 299px; }
  .col-edition { left: 628px; width: 560px; bottom: 18px; }

  .category-header {
    position: relative; height: 141px;
    background: radial-gradient(ellipse at 50% 0%, var(--header-mid), var(--header-dark) 75%);
    overflow: hidden;
  }
  .category-thumb {
    position: absolute; left: 12px; top: 12px; width: 84px; height: 84px;
    border: 2px solid #c9d3dd; border-radius: 6px;
  }
  .thumb-supplies { background: linear-gradient(135deg, #f4f6f8, #b7c2cc); }
  .thumb-world { background: linear-gradient(135deg, #b9a77e, #e6a43a 55%, #8a7a5a); }
  .header-lines {
    position: absolute; left: 108px; top: 17px;
    font-family: "Open Sans", Arial, sans-serif; font-size: 13.5px; line-height: 17.5px;
    letter-spacing: 1px; color: var(--muted); list-style: none; white-space: nowrap;
  }
  .header-lines li:first-child { color: var(--white); }
  .col-maps .header-lines {
    left: 105px; top: 20px; letter-spacing: -0.2px; font-size: 11.5px; line-height: 15.5px;
  }

  .tab-bar {
    position: relative; height: 36px; background: var(--tab-blue);
    color: var(--white); font-family: "Open Sans", Arial, sans-serif;
    font-size: 17px; letter-spacing: 1.2px; line-height: 36px; padding-left: 10px;
  }
  .tab-bar svg { position: absolute; right: 0; top: 0; }

  .group-bar {
    height: 25px; margin-top: 7px; background: linear-gradient(var(--green-light), var(--green));
    color: var(--white); font-weight: 700; font-size: 14px; line-height: 25px; padding-left: 10px;
  }
  .item-list { list-style: none; }
  .item-list li {
    height: 72px; line-height: 72px; padding-left: 10px; font-size: 13.5px;
    border-bottom: 1px solid var(--rule);
  }
  .item-list li:last-child { border-bottom: 0; height: 70px; }
  .group-bar.second { margin-top: 0; }
  .group-pale { height: 30px; background: var(--green-pale); }

  .item-active {
    position: relative; height: 72px; background: var(--green-pale);
    font-size: 13.5px; padding: 22px 0 0 10px;
  }
  .item-active svg { position: absolute; right: 8px; top: 11px; }

  .edition-header { background: linear-gradient(180deg, #0d2848, #1f4b7a); }
  .edition-map {
    position: absolute; left: 250px; top: 0; width: 310px; height: 141px;
    background: radial-gradient(ellipse at 55% 45%, var(--map-yellow), var(--map-orange) 55%, rgba(243,149,31,0) 80%);
  }
  .region {
    position: absolute; font-family: "Open Sans", Arial, sans-serif;
    color: rgba(255,255,255,0.22); letter-spacing: 1px; white-space: nowrap;
  }
  .edition-title {
    position: absolute; left: 20px; top: 82px; font-family: "Open Sans", Arial, sans-serif;
    font-size: 29px; color: var(--white); letter-spacing: 1.5px; white-space: nowrap;
  }
  .category-tabs {
    position: relative; height: 25px; margin-top: 7px;
    background: linear-gradient(var(--green-light), var(--green));
  }
  .category-tab {
    position: absolute; left: 2px; top: 2px; height: 23px; padding: 0 6px;
    background: #f2f7ec; font-size: 13.5px; line-height: 23px;
  }
  .category-tab svg { position: absolute; left: 34px; top: 23px; }

  .listing { position: relative; padding: 0 11px; }
  .rule { border-top: 1px dotted #999; }
  .rule.top { margin-top: 40px; }
  .product { position: relative; height: 141px; }
  .product-thumb {
    position: absolute; left: 25px; top: 22px; width: 84px; height: 44px;
    background: linear-gradient(90deg, var(--map-orange), var(--map-yellow) 50%, var(--map-orange));
    border-radius: 40% 30% 45% 35%;
  }
  .product-name {
    position: absolute; left: 169px; top: 23px; color: var(--green);
    font-weight: 700; font-size: 17px;
  }
  .product-meta { position: absolute; left: 169px; top: 50px; font-weight: 700; font-size: 13.5px; }
  .product-more { position: absolute; left: 15px; top: 101px; font-weight: 700; font-size: 14px; }
  .pager {
    display: flex; justify-content: space-between; padding: 19px 2px 0;
    font-size: 13.5px;
  }
</style>
</head>
<body>

<section class="column col-products">
  <header class="category-header">
    <div class="category-thumb thumb-supplies" role="img" aria-label="Abbildung: Landkarten-Zubehör"></div>
    <ul class="header-lines">
      <li>Landkarten und Zubehör</li>
      <li>Software + Daten</li>
      <li>Sonderanfertigungen</li>
      <li>Werbemittel</li>
      <li>Dekoratives</li>
    </ul>
  </header>
  <div class="tab-bar">Landkarten und Zubehör
    <svg width="40" height="36" viewBox="0 0 40 36"><path d="M14 0h10l16 18-16 18H14l16-18z" fill="var(--tab-blue-dark)"/></svg>
  </div>
  <div class="group-bar">Software</div>
  <ul class="item-list">
    <li>GeoPlaner</li>
    <li>LIVE-DEMO</li>
    <li>OrtFinder (Standortsuche)</li>
  </ul>
  <div class="group-bar second">Daten</div>
  <div class="group-pale"></div>
</section>

<section class="column col-maps">
  <header class="category-header">
    <div class="category-thumb thumb-world" role="img" aria-label="Abbildung: Weltkarte"></div>
    <ul class="header-lines">
      <li>Landkarten geografisch sortiert</li>
      <li>Landkarten sortiert nach Thema</li>
      <li>Landkarten digital</li>
      <li>Individuelle Einzelanfertigungen</li>
      <li>Zubehör</li>
      <li>Verarbeitung</li>
    </ul>
  </header>
  <div class="tab-bar">Wandkarten
    <svg width="40" height="36" viewBox="0 0 40 36"><path d="M14 0h10l16 18-16 18H14l16-18z" fill="var(--tab-blue-dark)"/></svg>
  </div>
  <div class="group-bar">Marktdaten und Geodaten (GIS)</div>
  <div class="item-active">Marktdaten + Geodaten (GIS)
    <svg width="12" height="16" viewBox="0 0 12 16"><path d="M0 0l12 8-12 8z" fill="var(--green)"/></svg>
  </div>
</section>

<section class="column col-edition">
  <header class="category-header edition-header">
    <div class="edition-map" role="img" aria-label="Illustration: Weltkarte in Orange"></div>
    <span class="region" style="left:76px;top:24px;font-size:16px">Asien</span>
    <span class="region" style="left:161px;top:32px;font-size:16px">Afrika</span>
    <span class="region" style="left:47px;top:52px;font-size:22px">Europa</span>
    <span class="region" style="left:62px;top:113px;font-size:14px">Australien</span>
    <span class="region" style="left:205px;top:103px;font-size:22px">Amerika</span>
    <div class="edition-title">Welt-Edition</div>
  </header>
  <div class="tab-bar">Welt-Edition
    <svg width="50" height="36" viewBox="0 0 50 36"><path d="M5 4h10l10 12 10-12h10L25 32z" fill="var(--tab-blue-dark)"/></svg>
  </div>
  <div class="category-tabs">
    <div class="category-tab">Kategorie 1
      <svg width="18" height="10" viewBox="0 0 18 10"><path d="M0 0h18L9 10z" fill="var(--green)"/></svg>
    </div>
  </div>
  <div class="listing">
    <div class="rule top"></div>
    <article class="product">
      <div class="product-thumb" role="img" aria-label="Abbildung: kleine Weltkarte"></div>
      <h2 class="product-name">Marktdaten</h2>
      <p class="product-meta">Nr.: &nbsp;·&nbsp; Größe:</p>
      <p class="product-more">mehr...</p>
    </article>
    <div class="rule"></div>
    <div class="pager">
      <span>Zeige <b>1</b> bis <b>1</b> (von insgesamt <b>1</b> Artikeln)</span>
      <span>Seiten: &nbsp;<b>1</b></span>
    </div>
  </div>
</section>

</body>
</html>
```